Global (re)insurance broker needs a business card design

We need a classic business card for our company that is headquartered in SG, with offices in Malaysia and Dubai. We specialise in insurance and reinsurance broking and consultancy for our global clients.

```html
<!DOCTYPE html>
<html lang="en">
<head>
<meta charset="utf-8">
<title>Meridale Business Card</title>
<link rel="stylesheet" href="https://fonts.googleapis.com/css2?family=Open+Sans:wght@400;600;700;800&display=swap">
<style>
  :root {
    --stage: #2a2a2c;
    --card-dark: #1f1f23;
    --brand-blue: #2547a3;
    --brand-blue-deep: #1d3a8c;
    --brand-mint: #c3e2bd;
    --ink-light: #f4f5f7;
    --divider: #8a8c94;
  }
  * { box-sizing: border-box; margin: 0; padding: 0; }
  html, body {
    width: 1200px; height: 780px; overflow: hidden;
    background: var(--stage);
    font-family: "Open Sans", Arial, sans-serif;
  }
  .stage {
    position: relative; width: 1200px; height: 780px;
    display: flex; align-items: center; justify-content: center; gap: 40px;
  }
  .card {
    position: relative; width: 540px; height: 308px; overflow: hidden;
    box-shadow: 0 14px 30px rgba(0,0,0,.45);
  }

  /* Back side */
  .card--back { background: var(--brand-blue); }
  .card--back .pattern-field {
    position: absolute; inset: 0;
    background: linear-gradient(160deg, var(--brand-blue) 0%, #2a4fb0 45%, var(--brand-blue-deep) 100%);
  }
  .card--back .back-wordmark {
    position: absolute; right: 46px; bottom: 112px;
    font-weight: 800; font-size: 17px; letter-spacing: .5px;
    color: var(--ink-light);
  }

  /* Front side */
  .card--front { background: var(--card-dark); color: var(--ink-light); }
  .wordmark {
    position: absolute; left: 150px; top: 52px;
    font-weight: 800; font-size: 74px; letter-spacing: 1px; line-height: 1;
    color: var(--brand-mint);
  }
  .holder { position: absolute; left: 56px; top: 186px; }
  .holder__name { font-weight: 800; font-size: 31px; line-height: 1.05; }
  .holder__first { color: var(--brand-blue); }
  .holder__last { color: var(--brand-mint); }
  .holder__role { font-weight: 600; font-size: 14px; margin-top: 2px; }
  .divider {
    position: absolute; left: 292px; top: 168px; width: 1px; height: 78px;
    background: var(--divider);
  }
  .contacts { position: absolute; left: 310px; top: 172px; list-style: none; }
  .contacts li {
    display: flex; align-items: center; gap: 8px;
    font-size: 13px; line-height: 23px;
  }
  .contacts svg { width: 13px; height: 13px; flex: none; }
  .address-band {
    position: absolute; left: 0; right: 0; top: 258px; height: 30px;
    background: var(--brand-blue);
    display: flex; align-items: center; padding-left: 56px;
    font-size: 13.5px; font-weight: 600; color: var(--ink-light);
  }
</style>
</head>
<body>
<main class="stage">
  <section class="card card--back" aria-label="Card back">
    <div class="pattern-field" role="img" aria-label="Repeating company name pattern in blue tones"></div>
    <div class="back-wordmark">MERIDALE</div>
  </section>

  <section class="card card--front" aria-label="Card front">
    <div class="wordmark">MERIDALE</div>

    <div class="holder">
      <p class="holder__name"><span class="holder__first">Rina</span> <span class="holder__last">Voss</span></p>
      <p class="holder__role">Chief Operating Officer</p>
    </div>

    <div class="divider"></div>

    <ul class="contacts">
      <li>
        <svg viewBox="0 0 14 14" aria-hidden="true"><rect x="3.5" y="1" width="7" height="12" rx="1.5" fill="none" stroke="#f4f5f7" stroke-width="1.2"/><circle cx="7" cy="11" r=".7" fill="#f4f5f7"/></svg>
        +65 9000 1234
      </li>
      <li>
        <svg viewBox="0 0 14 14" aria-hidden="true"><circle cx="7" cy="7" r="6" fill="#2547a3"/><path d="M1 7h12M7 1c-2.5 3-2.5 9 0 12M7 1c2.5 3 2.5 9 0 12" fill="none" stroke="#c3e2bd" stroke-width=".8"/></svg>
        www.meridale.com
      </li>
      <li>
        <svg viewBox="0 0 14 14" aria-hidden="true"><rect x="1" y="3" width="12" height="9" rx="1" fill="none" stroke="#c3e2bd" stroke-width="1.2"/><path d="M1.5 3.5 7 8l5.5-4.5" fill="none" stroke="#c3e2bd" stroke-width="1.2"/></svg>
        rina@meridale.com
      </li>
    </ul>

    <div class="address-band">48 Harbour Lane, Quayside Tower #08-02, Singapore 049100</div>
  </section>
</main>
</body>
</html>
```